K & R Acre Works. Business card design

We need a business card designed for a new business. We have a bulldozer and tractor service. We clear land and make wildlife food plots. We provide disking, bush hogging, and site prep services.
I have attached an image of a business card that I like and would like my business cards to look similar.

Target Market(s)

anyone needing bulldozer and/or tractor services

Industry/Entity Type

Business

Contact Information for Business Card

K & R Acre Works, Operated by 7-T-Ranch
Wade Colton
601-472-3358
wcr4817@fieldmail-example.com

Font styles to use
Sans Serif

Colors

Designer to choose colors to be used in the design.

Requirements
Must have
• image of tractor and bulldozer
• Land Clearing
• Wildlife food plots
• Bush Hogging
• Disking
• Site prep
Nice to have
• i have included a image of a business card that i like. I would like mine to be similar.

```html
<!DOCTYPE html>
<html lang="en">
<head>
<meta charset="utf-8">
<title>K &amp; R Acre Works – Business Card</title>
<link rel="stylesheet" href="https://fonts.googleapis.com/css2?family=Oswald:wght@300;400;500&family=Raleway:wght@300;400&display=swap">
<style>
  :root {
    --page: #e9e6e1;
    --forest-dark: #1c2619;
    --forest-mid: #33472a;
    --forest-light: #4f6b35;
    --machine: #8a8a3a;
    --accent-red: #ec4a3c;
    --paper-white: #f4f4f4;
    --ink-white: #ffffff;
  }
  * { margin: 0; padding: 0; box-sizing: border-box; }
  html, body { width: 1200px; height: 1023px; overflow: hidden; }
  body { background: var(--page); position: relative; }

  .card {
    position: absolute; left: 100px; top: 226px;
    width: 1000px; height: 570px;
    border-radius: 14px; overflow: hidden;
    box-shadow: 0 10px 30px rgba(0,0,0,.25);
  }
  .card__photo {
    position: absolute; inset: 0;
    background:
      radial-gradient(ellipse 38% 30% at 48% 58%, var(--machine) 0%, rgba(138,138,58,0) 70%),
      radial-gradient(ellipse 60% 50% at 60% 40%, var(--forest-light) 0%, rgba(79,107,53,0) 75%),
      linear-gradient(160deg, var(--forest-mid) 0%, var(--forest-dark) 80%);
  }
  .card__shade {
    position: absolute; inset: 0;
    background: linear-gradient(90deg, rgba(10,14,9,.65) 0%, rgba(10,14,9,.15) 55%, rgba(10,14,9,.35) 100%);
  }

  .company {
    position: absolute; left: 58px; top: 54px;
  }
  .company__name {
    font-family: 'Oswald', sans-serif; font-weight: 500;
    font-size: 58px; line-height: 1; color: var(--accent-red);
    text-transform: uppercase; letter-spacing: .5px;
  }
  .company__operator {
    margin-top: 12px;
    font-family: 'Raleway', sans-serif; font-weight: 300;
    font-size: 26px; color: var(--ink-white);
    text-transform: uppercase; letter-spacing: 7px;
  }

  .owner {
    position: absolute; right: 60px; top: 60px;
    font-family: 'Oswald', sans-serif; font-weight: 400;
    font-size: 52px; color: var(--accent-red);
    text-transform: uppercase; letter-spacing: .5px;
  }
  .divider {
    position: absolute; left: 58px; top: 250px;
    width: 660px; height: 3px; background: var(--ink-white);
  }

  .contact { position: absolute; left: 58px; top: 280px; }
  .contact__row {
    display: flex; align-items: center; gap: 16px;
    font-family: 'Raleway', sans-serif; font-weight: 400;
    font-size: 34px; color: var(--ink-white); line-height: 46px;
  }
  .contact__icon { width: 22px; height: 22px; flex: none; }

  .services {
    position: absolute; left: 96px; top: 392px;
    font-family: 'Oswald', sans-serif; font-weight: 400;
    font-size: 25px; line-height: 32px; color: var(--ink-white);
    text-transform: uppercase;
  }

  .card__band { position: absolute; left: 0; bottom: 0; width: 1000px; height: 80px; }
</style>
</head>
<body>
  <div class="card">
    <div class="card__photo" role="img" aria-label="Photo of a bulldozer and tractor clearing brush in a green wooded lot"></div>
    <div class="card__shade"></div>

    <div class="company">
      <div class="company__name">K &amp; R Acre Works</div>
      <div class="company__operator">Operated by 7-T-Ranch</div>
    </div>

    <div class="owner">Wade Colton</div>
    <div class="divider"></div>

    <div class="contact">
      <div class="contact__row">
        <svg class="contact__icon" viewBox="0 0 24 24"><path fill="#ec4a3c" d="M6.6 10.8a15 15 0 0 0 6.6 6.6l2.2-2.2c.3-.3.7-.4 1-.2 1.1.4 2.3.6 3.6.6.6 0 1 .4 1 1V20c0 .6-.4 1-1 1A17 17 0 0 1 3 4c0-.6.4-1 1-1h3.5c.6 0 1 .4 1 1 0 1.3.2 2.5.6 3.6.1.3 0 .7-.2 1z"/></svg>
        <span>601-472-3358</span>
      </div>
      <div class="contact__row">
        <svg class="contact__icon" viewBox="0 0 24 24"><rect x="2" y="5" width="20" height="14" fill="none" stroke="#ec4a3c" stroke-width="2"/><path d="M2 5l10 8 10-8" fill="none" stroke="#ec4a3c" stroke-width="2"/></svg>
        <span>wcr4817@fieldmail-example.com</span>
      </div>
    </div>

    <div class="services">
      <div>Land Clearing - Wildlife Food Plots</div>
      <div>Bush Hogging - Disking - Site Prep</div>
    </div>

    <svg class="card__band" viewBox="0 0 1000 80" preserveAspectRatio="none">
      <polygon points="0,62 1000,62 1000,80 0,80" fill="#f4f4f4"/>
      <polygon points="600,0 1000,0 1000,80 540,80" fill="#ec4a3c"/>
    </svg>
  </div>
</body>
</html>
```